RW Holloway LLC Business Card - Civil Engineering & Consulting Firm

We need a Business Card that is elegant, and masculine.  It is our Professional Civil Engineering & Consulting Company located in San Antonio TX (Not s construction or builder firm- no gears & no tool images please). We provide civil engineering services including  commercial site plans, grading and drainage plans, utility plans, hydraulics and hydrology, land planning, utility coordination, and other general civil engineering services related to commercial and residential development.
We have 2 existing Logos. We would like to convey reliability, strength, trustworthiness and attention to detail.  Blues and orange tones as per logo We are OK with the use of a darker blue in the mix.  We have 2 logo versions - Full Company Name Logo to go on the back of card, & Small Icon Logo for the front w/ personal Info.

Target Market(s)
Architects, Real Estate Developers, Other Strctural Engineers, Surveyers, General Contractors
Industry/Entity Type
Professional Civil Engineering
Contact Information for Business Card
Name, Position, Address, Cell & Office #, email, and company website
Font styles to use
Other font styles liked:
- Avian
Requirements
Should not have
- No Tools, No Gears, no Cranes, or Construction Equipment.

```html
<!DOCTYPE html>
<html lang="en">
<head>
<meta charset="utf-8">
<title>RW Holloway LLC Business Card</title>
<link href="https://fonts.googleapis.com/css2?family=Arimo:wght@400;700&display=swap" rel="stylesheet">
<style>
  :root {
    --backdrop: #141416;
    --card-navy: #0c0c33;
    --pattern-navy: #17174a;
    --edge-orange: #d9781c;
    --accent-orange: #f39a1e;
    --logo-blue: #6aa3d8;
    --text-white: #f2f2f5;
  }
  * { margin: 0; padding: 0; box-sizing: border-box; }
  html, body {
    width: 1200px; height: 963px; overflow: hidden;
    background: var(--backdrop);
    font-family: "Arimo", Arial, sans-serif;
  }
  .sheet {
    width: 1200px; height: 963px;
    display: flex; align-items: center; justify-content: center; gap: 60px;
  }
  .card {
    position: relative;
    width: 520px; height: 298px;
    background: var(--card-navy);
    border-radius: 22px;
    border: 2px solid var(--edge-orange);
    overflow: hidden;
  }
  /* Front */
  .card-front { display: flex; align-items: center; padding: 0 36px; }
  .front-mark {
    width: 190px; display: flex; align-items: center; gap: 10px;
  }
  .front-mark .mark-square {
    width: 14px; height: 14px; background: var(--logo-blue); flex: none;
  }
  .front-mark .mark-name {
    color: var(--logo-blue); font-size: 17px; font-weight: 700; line-height: 1.2;
  }
  .contact { color: var(--text-white); font-size: 15px; line-height: 1.3; }
  .contact .person-name {
    color: var(--accent-orange); font-weight: 700; font-size: 18px;
    text-transform: uppercase; letter-spacing: 0.5px;
  }
  .contact .role { margin-bottom: 8px; }
  .contact .address { margin-bottom: 8px; }
  .contact .line { display: flex; align-items: center; gap: 8px; }
  .contact .line svg { width: 13px; height: 13px; flex: none; }
  /* Back */
  .back-pattern {
    position: absolute; inset: 0;
    background: linear-gradient(135deg, var(--pattern-navy), var(--card-navy));
  }
  .back-name {
    position: absolute; right: 40px; bottom: 70px;
    color: var(--logo-blue); font-size: 34px; font-weight: 400; letter-spacing: 2px;
  }
</style>
</head>
<body>
<main class="sheet">
  <section class="card card-front" aria-label="Business card front">
    <div class="front-mark">
      <span class="mark-square"></span>
      <span class="mark-name">RW Holloway LLC</span>
    </div>
    <div class="contact">
      <p class="person-name">Daniel Reyes</p>
      <p class="role">Manager</p>
      <p class="address">Your address, city<br>state, ZIP 0000</p>
      <p class="line">
        <svg viewBox="0 0 16 16" aria-hidden="true"><path d="M3 1h3l1 4-2 1a9 9 0 0 0 5 5l1-2 4 1v3a2 2 0 0 1-2 2A13 13 0 0 1 1 3a2 2 0 0 1 2-2z" fill="var(--accent-orange)"/></svg>
        123-456-2100
      </p>
      <p class="line">
        <svg viewBox="0 0 16 16" aria-hidden="true"><rect x="4" y="1" width="8" height="14" rx="1.5" fill="none" stroke="var(--accent-orange)" stroke-width="1.6"/><circle cx="8" cy="12.5" r="0.9" fill="var(--accent-orange)"/></svg>
        123-456-2100
      </p>
      <p class="line">
        <svg viewBox="0 0 16 16" aria-hidden="true"><rect x="1" y="3" width="14" height="10" fill="none" stroke="var(--accent-orange)" stroke-width="1.6"/><path d="M1 3l7 6 7-6" fill="none" stroke="var(--accent-orange)" stroke-width="1.6"/></svg>
        name@rwholloway.com
      </p>
      <p class="line">
        <svg viewBox="0 0 16 16" aria-hidden="true"><circle cx="8" cy="8" r="6.5" fill="none" stroke="var(--accent-orange)" stroke-width="1.5"/><ellipse cx="8" cy="8" rx="3" ry="6.5" fill="none" stroke="var(--accent-orange)" stroke-width="1.2"/><path d="M1.5 8h13" stroke="var(--accent-orange)" stroke-width="1.2"/></svg>
        www.rwholloway.com
      </p>
    </div>
  </section>

  <section class="card card-back" aria-label="Business card back">
    <div class="back-pattern" role="img" aria-label="Repeating tonal pattern of the company mark across the card"></div>
    <p class="back-name">RW Holloway LLC</p>
  </section>
</main>
</body>
</html>
```